Ledger Tide Folk Banner Ad campaign

We are the number 1 leading automated journal & analytics platform for active traders in the crypto space

We will be running banner ads on a specialist ad network and need HTML designs + a good strategy.

Some of our key selling points to consider including:

- The #1 automated journaling & analytics solution for Crypto Traders
- We save traders time (from manual data entry that can be automated by our journal trade import service)
- We help traders improve through detailed analytics feedback on their trading performance
- LTF has helped thousands of crypto traders improve performance
- 5,700+ traders are using LTF to save themselves hundreds of data entry hours per year
- Analyse your full trade history in a click!

I have attached an example mockup we came up with internally but we are not professionals. Use it as a guide to heavily improve upon in the context of general design quality, and 'sales-y' lingo to improve conversions
Updates

Have added a £100 1st place payment increase upon advice from a designer Should incentivise the best of the best to submit work

Target Market(s)

Active traders in the crypto derivatives space. Trading on the following exchanges:

- Zorvex.com
- Quillaro.com
- Tavomen.com
- KWP.com

Font styles to use
Other font styles liked:
• Quicksand is our main font atm

Colors
3277b5
33a6d7
0792cd
85abd2
3276b5
85acd3
85cae6
86cae7

Requirements
Must have
• similar colour scheme from my example upload.

Check our main website for more: ledgertidefolk.example

Although bare in mind, its a bit old and shitty. We are now working with specialists to improve, so feel free to have some creative freedom
Nice to have
• Nice clear custom icons to accompany text. And a rotation of 2 or 3 of the main selling points from the project description

```html
<!DOCTYPE html>
<html lang="en">
<head>
<meta charset="utf-8">
<title>Ledger Tide Folk — Banner Set</title>
<link rel="stylesheet" href="https://fonts.googleapis.com/css2?family=Quicksand:wght@400;500;600;700&display=swap">
<style>
  :root {
    --page-bg: #efefef;
    --brand-blue: #3277b5;
    --brand-sky: #85cae6;
    --screen-blue: #86cae7;
    --screen-deep: #85abd2;
    --cta-yellow: #f9f21b;
    --highlight-yellow: #f5ef1e;
    --text-light: #ffffff;
    --text-dark: #141414;
  }
  * { box-sizing: border-box; margin: 0; padding: 0; }
  html, body {
    width: 1013px; height: 1200px; overflow: hidden;
    background: var(--page-bg);
    font-family: "Quicksand", sans-serif;
  }
  .banner-sheet { position: relative; width: 1013px; height: 1200px; }
  .banner {
    position: absolute; width: 383px; height: 320px;
    background: var(--brand-sky); overflow: hidden;
  }
  .banner--left { left: 102px; }
  .banner--right { left: 528px; }
  .banner--row1 { top: 44px; }
  .banner--row2 { top: 432px; }
  .banner--row3 { top: 836px; }

  .banner__top {
    position: absolute; left: 0; top: 0; width: 100%; height: 199px;
    background: var(--brand-blue);
  }
  .brand {
    position: absolute; left: 55px; top: 29px;
    display: flex; align-items: center; gap: 15px;
    color: var(--text-light); font-weight: 400; font-size: 19px; letter-spacing: 0.5px;
  }
  .brand__mark {
    width: 14px; height: 14px; border: 1.5px solid var(--text-light); border-radius: 2px;
  }
  .monitor {
    position: absolute; left: 47px; top: 75px; width: 117px; height: 106px;
    background: linear-gradient(180deg, var(--screen-blue), var(--screen-deep));
    border-radius: 6px;
  }
  .monitor--shift-a { left: 51px; }
  .monitor--shift-b { left: 56px; }
  .monitor--raised { top: 74px; }

  .banner__copy {
    position: absolute; left: 174px; color: var(--text-light); font-weight: 500;
  }
  .hl { color: var(--highlight-yellow); }

  .copy--rank { top: 74px; left: 175px; font-size: 16px; line-height: 21.5px; }
  .copy--rank .rank-head { display: block; line-height: 30px; }
  .copy--rank .rank-lead { font-size: 16px; }
  .copy--rank .rank-num { font-size: 28px; font-weight: 700; }

  .copy--time { top: 95px; left: 183px; }
  .copy--time .time-head { font-size: 26px; line-height: 30px; font-weight: 500; }
  .copy--time .time-head-big { font-size: 30px; }
  .copy--time .time-note { font-size: 7.5px; line-height: 10px; text-align: center; margin-top: 6px; font-weight: 500; }

  .copy--improve { top: 76px; left: 178px; font-size: 14.5px; line-height: 20px; }
  .copy--users { top: 86px; left: 182px; font-size: 14.5px; line-height: 20px; }
  .copy--users .users-head { font-size: 18.5px; line-height: 22px; display: block; }
  .copy--thousands { top: 94px; left: 181px; font-size: 13.5px; line-height: 17.5px; }
  .copy--analyse { top: 87px; left: 189px; font-size: 15.5px; line-height: 22px; }
  .copy--analyse .analyse-head { font-size: 23px; line-height: 26px; display: block; }

  .cta {
    position: absolute; left: 75px; top: 231px; width: 232px; height: 43px;
    border-radius: 22px; background: var(--cta-yellow);
    display: flex; align-items: center; justify-content: center;
    color: var(--text-dark); font-weight: 600; font-size: 13px; letter-spacing: 0.2px;
    box-shadow: 2px 3px 5px rgba(20, 60, 110, 0.25);
  }
</style>
</head>
<body>
<main class="banner-sheet">

  <section class="banner banner--left banner--row1">
    <div class="banner__top"></div>
    <div class="brand"><span class="brand__mark"></span>LEDGER TIDE FOLK</div>
    <div class="monitor" role="img" aria-label="Monitor illustration showing dashboard charts"></div>
    <p class="banner__copy copy--rank">
      <span class="rank-head"><span class="rank-lead">The </span><span class="rank-num hl">#1</span></span>
      Automated Journaling &amp;<br>Analytics Solution for<br>Crypto Traders
    </p>
    <a class="cta">START YOUR FREE TRIAL NOW</a>
  </section>

  <section class="banner banner--right banner--row1">
    <div class="banner__top"></div>
    <div class="brand"><span class="brand__mark"></span>LEDGER TIDE FOLK</div>
    <div class="monitor" role="img" aria-label="Monitor illustration showing dashboard charts"></div>
    <div class="banner__copy copy--time">
      <p class="time-head">We <span class="hl">save</span></p>
      <p class="time-head time-head-big">traders time</p>
      <p class="time-note">(from manual data entry that can be automated<br>by our journal trade import service)</p>
    </div>
    <a class="cta">START YOUR FREE TRIAL NOW</a>
  </section>

  <section class="banner banner--left banner--row2">
    <div class="banner__top"></div>
    <div class="brand"><span class="brand__mark"></span>LEDGER TIDE FOLK</div>
    <div class="monitor monitor--shift-a" role="img" aria-label="Monitor illustration showing dashboard charts"></div>
    <p class="banner__copy copy--improve">
      We help <span class="hl">traders improve</span><br>through detailed analytics<br>feedback on their trading<br>performance
    </p>
    <a class="cta">START YOUR FREE TRIAL NOW</a>
  </section>

  <section class="banner banner--right banner--row2">
    <div class="banner__top"></div>
    <div class="brand"><span class="brand__mark"></span>LEDGER TIDE FOLK</div>
    <div class="monitor monitor--raised" role="img" aria-label="Monitor illustration showing dashboard charts"></div>
    <p class="banner__copy copy--users">
      <span class="users-head hl">5,700+ traders</span>
      are using&nbsp; LTF to save<br>themselves hundreds of<br>data entry hours per year
    </p>
    <a class="cta">START YOUR FREE TRIAL NOW</a>
  </section>

  <section class="banner banner--left banner--row3">
    <div class="banner__top"></div>
    <div class="brand"><span class="brand__mark"></span>LEDGER TIDE FOLK</div>
    <div class="monitor monitor--shift-a" role="img" aria-label="Monitor illustration showing dashboard charts"></div>
    <p class="banner__copy copy--thousands">
      <span class="hl">LTF</span> has helped thousands<br>of crypto traders improve<br>performance
    </p>
    <a class="cta">START YOUR FREE TRIAL NOW</a>
  </section>

  <section class="banner banner--right banner--row3">
    <div class="banner__top"></div>
    <div class="brand"><span class="brand__mark"></span>LEDGER TIDE FOLK</div>
    <div class="monitor monitor--shift-b" role="img" aria-label="Monitor illustration showing dashboard charts"></div>
    <p class="banner__copy copy--analyse">
      <span class="analyse-head hl">Analyse</span>
      your full trade history<br>in a click!
    </p>
    <a class="cta">START YOUR FREE TRIAL NOW</a>
  </section>

</main>
</body>
</html>
```